New, modern business card for growing audiology practice

We need a new business card for our audiology practice. Our logo and website have recently changed (more modern) and we want our business cards to reflect this change.
We conduct hearing tests, perform earwax removals, and fit & dispense hearing aids to our patients. We are a family owned practice in which the owner is the one who works directly with the patient. I have attached logos in various formats to use, as well as two ideas I found on this website; as well as a scanned copy of our current logo. Good luck!

Industry/Entity Type

Business

Contact Information for Business Card

Company name: Tolvera Hearing Center
Provider name: Peter Wolstenby, Au.D. F/NSB
Phone number: (440) 683-5127
Address: 837 W. Lindell Ave. Marlow Falls, OH 44187
email: tolverahearing@postvane.com
website: tolverahearing.com

Colors
000000
aaaaaa
dbdbdb
cacaca
9bcb3c
afd23c
cadf82
b1b1b1

Requirements
Must have
• My card must include information in the "details" section. In the attached images, I found a few that I liked and I would like to model after - "brisky bouncin'" and "Sound Method Center".
• Must be horizontal.
• Must include logos provided. I uploaded them in various file formats and various ways.
• Must match logo font, if possible, if not, please get as close as you can.
Nice to have
• I really like the idea of having a color on one side with just the logo and company name and the contact information and provider name on the other side. I also really like the idea of having the main color dominating on the logo/company side with accent of that same color on the contact side of the card.
Should not have
• Must not be vertical.

```html
<!DOCTYPE html>
<html lang="en">
<head>
<meta charset="utf-8">
<title>Tolvera Hearing Center – Business Card</title>
<link href="https://fonts.googleapis.com/css2?family=Roboto:wght@400;500;700&family=Roboto+Condensed:wght@700&display=swap" rel="stylesheet">
<style>
  :root {
    --backdrop: #6f5a48;
    --card-white: #f3f3f3;
    --ink: #111111;
    --text-grey: #555555;
    --divider: #b1b1b1;
    --green: #6f9f34;
    --green-bright: #8fbf3c;
    --black: #000000;
    --white: #ffffff;
  }
  * { margin: 0; padding: 0; box-sizing: border-box; }
  html, body { width: 1200px; height: 960px; overflow: hidden; }
  body {
    background: var(--backdrop);
    position: relative;
    font-family: "Roboto", Arial, sans-serif;
  }
  .card {
    position: absolute;
    width: 600px;
    height: 342px;
    box-shadow: 0 3px 8px rgba(0,0,0,0.35);
  }
  .card-front { left: 314px; top: 113px; background: var(--card-white); overflow: hidden; }
  .card-back { left: 311px; top: 472px; background: var(--black); }

  .brand {
    position: absolute;
    display: flex;
    align-items: center;
    text-transform: uppercase;
    white-space: nowrap;
    font-weight: 400;
  }
  .brand-dot { border-radius: 50%; background: var(--green); flex: none; }
  .card-front .brand { left: 46px; top: 160px; font-size: 17.5px; color: var(--ink); gap: 8px; }
  .card-front .brand-dot { width: 14px; height: 14px; }
  .card-back .brand { left: 0; right: 0; top: 156px; justify-content: center; font-size: 29px; color: var(--white); gap: 14px; }
  .card-back .brand-dot { width: 22px; height: 22px; }

  .divider {
    position: absolute; left: 318px; top: 84px;
    width: 1px; height: 178px;
    background: linear-gradient(to bottom, transparent, var(--divider) 20%, var(--divider) 80%, transparent);
  }
  .contact { position: absolute; left: 349px; top: 90px; }
  .provider-name {
    font-family: "Roboto Condensed", "Arial Narrow", sans-serif;
    font-weight: 700; font-size: 21px; color: var(--green);
    text-transform: uppercase; line-height: 24px;
  }
  .provider-title { font-size: 15px; font-weight: 500; color: var(--ink); line-height: 20px; margin-top: 1px; }
  .address { margin-top: 10px; font-size: 14px; color: var(--text-grey); line-height: 18px; }
  .details { list-style: none; margin-top: 8px; font-size: 14px; color: var(--text-grey); }
  .details li { display: flex; align-items: center; gap: 9px; line-height: 19px; }
  .details svg { width: 14px; height: 14px; fill: var(--green); flex: none; }

  .accent-band { position: absolute; left: 0; bottom: 0; width: 600px; height: 22px; }

  .web-address {
    position: absolute; left: 0; right: 0; top: 288px;
    text-align: center; font-size: 14px; letter-spacing: 5px; color: var(--white);
  }
  .web-address .highlight { color: var(--green-bright); }
</style>
</head>
<body>
  <section class="card card-front">
    <div class="brand"><span class="brand-dot"></span>Tolvera Hearing Center</div>
    <div class="divider"></div>
    <div class="contact">
      <div class="provider-name">Peter Wolstenby</div>
      <div class="provider-title">AU.D. F/NSB</div>
      <div class="address">837 W. Lindell Ave.<br>Marlow Falls, OH 44187</div>
      <ul class="details">
        <li><svg viewBox="0 0 16 16"><path d="M3.5 1l2.5 3-1.5 2c.8 2 2.5 3.7 4.5 4.5l2-1.5 3 2.5-1.5 2.5C7 15 1 9 1 2.5z"/></svg>(440) 683-5127</li>
        <li><svg viewBox="0 0 16 16"><path d="M1 3h14v1.5L8 9 1 4.5z M1 6.5l7 4.5 7-4.5V13H1z"/></svg>tolverahearing@postvane.com</li>
        <li><svg viewBox="0 0 16 16"><circle cx="8" cy="8" r="7"/></svg>tolverahearing.com</li>
      </ul>
    </div>
    <svg class="accent-band" viewBox="0 0 600 22" preserveAspectRatio="none">
      <polygon points="0,0 390,0 384,22 0,22" fill="var(--green)"/>
      <polygon points="392,0 396,0 390,22 386,22" fill="var(--white)"/>
      <polygon points="398,0 600,0 600,22 392,22" fill="var(--black)"/>
    </svg>
  </section>

  <section class="card card-back">
    <div class="brand"><span class="brand-dot"></span>Tolvera Hearing Center</div>
    <div class="web-address">www.<span class="highlight">tolverahearing</span>.com</div>
  </section>
</body>
</html>
```